Visitenkarten-Design für virtuelle Jobmesse & Jobbörse für Soldaten
Zielgruppe
Die KVL GmbH ist ein Unternehmen das zwei Hauptprodukte betreibt! Zum einen Jobbörse für Soldaten unter www.laufbahnwechsel-beispiel.de und zum anderen eine virtuelle Jobmesse für Soldaten unter www.merivon-beispiel.de , die wir zweimal im Jahr veranstalten.
Aufgabenstellung
Wir haben ja die beiden Produkte Laufbahnwechsel.de und die Merivon, für die bereits jeweils ein separtes Logo besteht! Diese finden Sie im Anhang! Beide werden doch jedoch von einem Unternehmen, der KVL GmbH betrieben! Aktuell nutzen wir eine Visitenkarte mit dem Logo von KVL und eine mit dem Logo der MERIVON. Gerade im Hinblick darauf, dass wir zukünftig auch weiter Plattformen in unser Portfolio aufnehmen, möchte ich hier unsere V-Karten flexibler gestalten!
Ziel soll es also sein, eine Visitenkarte zu gestalten, auf dem klar wird, dass der Mitarbeiter von der KVL GmbH kommt, die KVL GmbH aber unterschiedliche Produkte betreibt.
Im Anhang finden Sie:
1. Das Logo von KVL
2. Das Logo von Merivon
3. Die aktuelle V-Karte von KVL
4. Die aktuelle V-Karte von MERIVON
Vielleicht ein kleiner Anreiz: Aktuell nutzen wir auch zwei getrennte Geschäftspapiere. Das von www.laufbahnwechsel-beispiel.de lade ich einmal hoch! Der Designer, der auch die Visitenkarte erstellt, erhällt im Anschluss den 1:1 Auftrag in Höhe von 200 Euro für die Erstellung des Geschäftspapiers! Wenn Sie jetzt schon einen Vorschlag für das Geschäftspapier einreichen, erhöht das natürlich Ihre Chancen, wobei ich verspreche, dass wir im Falle eine Annahme das 1:1 im Anschluß dennoch starten werden!

```html
<!DOCTYPE html>
<html lang="de">
<head>
<meta charset="utf-8">
<title>Visitenkarten – KVL GmbH</title>
<link href="https://fonts.googleapis.com/css2?family=Arimo:wght@400;700&display=swap" rel="stylesheet">
<style>
  :root {
    --brand-blue: #1f4a7b;
    --brand-green: #3e5b2d;
    --text-grey: #858585;
    --card-border: #5a5a5a;
    --paper: #ffffff;
  }
  html, body {
    margin: 0;
    padding: 0;
    width: 848px;
    height: 1200px;
    overflow: hidden;
    background: var(--paper);
    font-family: "Arimo", Arial, sans-serif;
  }
  .sheet {
    position: relative;
    width: 848px;
    height: 1200px;
  }
  .card {
    position: absolute;
    top: 198px;
    width: 342px;
    height: 221px;
    border: 1px solid var(--card-border);
    box-sizing: border-box;
    background: var(--paper);
    overflow: hidden;
  }
  .card--laufbahn { left: 75px; --accent: var(--brand-blue); }
  .card--merivon { left: 441px; --accent: var(--brand-green); }

  .card__panel {
    position: absolute;
    left: 0;
    top: 0;
    width: 342px;
    height: 221px;
  }
  .card__panel path { fill: var(--accent); }

  .holder {
    position: absolute;
    left: 17px;
    top: 86px;
    color: #fff;
    white-space: nowrap;
  }
  .holder__name {
    font-weight: 700;
    font-size: 15.5px;
    letter-spacing: 0.3px;
    line-height: 18px;
  }
  .holder__role {
    font-size: 11px;
    line-height: 14px;
  }

  .brand-mark {
    position: absolute;
    top: 10px;
    display: flex;
    align-items: center;
    gap: 5px;
    height: 60px;
    color: var(--accent);
    font-weight: 700;
    white-space: nowrap;
  }
  .card--laufbahn .brand-mark { left: 231px; width: 100px; justify-content: center; font-size: 10.5px; letter-spacing: 0.2px; }
  .card--merivon .brand-mark { left: 214px; width: 118px; justify-content: center; font-size: 16px; letter-spacing: 0.5px; }
  .brand-mark__dot {
    width: 12px;
    height: 12px;
    border-radius: 50%;
    background: var(--accent);
    flex: none;
  }

  .contact {
    position: absolute;
    left: 158px;
    top: 84px;
    right: 0;
    color: var(--text-grey);
    font-size: 10.5px;
    white-space: nowrap;
  }
  .contact__brand {
    margin-left: 19px;
    font-weight: 700;
    font-size: 15.5px;
    line-height: 17px;
    color: var(--accent);
    letter-spacing: 0.2px;
  }
  .contact__owner {
    margin-left: 19px;
    line-height: 13px;
    margin-bottom: 5px;
  }
  .contact__row {
    display: flex;
    align-items: flex-start;
    margin-bottom: 4.5px;
    line-height: 14px;
  }
  .contact__icon {
    width: 14px;
    height: 14px;
    margin-right: 5px;
    flex: none;
    fill: var(--text-grey);
    stroke: var(--text-grey);
  }
  .contact__row--address .contact__icon { height: 18px; margin-top: 1px; }
</style>
</head>
<body>
<main class="sheet">

  <article class="card card--laufbahn">
    <svg class="card__panel" viewBox="0 0 342 221" aria-hidden="true">
      <path d="M0 0 H114 A157 157 0 0 1 103 221 H0 Z"/>
    </svg>
    <div class="brand-mark"><span>LAUFBAHNWECHSEL</span></div>
    <div class="holder">
      <div class="holder__name">Jonas Vetter</div>
      <div class="holder__role">Position</div>
    </div>
    <div class="contact">
      <div class="contact__brand">Laufbahnwechsel.de</div>
      <div class="contact__owner">eine Marke der KVL GmbH</div>
      <div class="contact__row contact__row--address">
        <svg class="contact__icon" viewBox="0 0 16 18" aria-hidden="true"><path d="M8 1a6 6 0 0 0-6 6c0 4.5 6 10 6 10s6-5.5 6-10a6 6 0 0 0-6-6z" fill="none" stroke-width="1.6"/><circle cx="8" cy="7" r="2.2" stroke="none"/></svg>
        <div>Lindenweg 14<br>86999 Erlenbach</div>
      </div>
      <div class="contact__row">
        <svg class="contact__icon" viewBox="0 0 16 14" aria-hidden="true"><path stroke="none" d="M3 1l2.5-.5 2 3.5-1.5 1.5c.8 1.8 2.2 3.2 4 4l1.5-1.5 3.5 2-.5 2.5c-.5 1-1.5 1.5-2.5 1.2C6.5 12.5 2.5 8.5 1.3 3.5 1 2.5 1.8 1.5 3 1z"/></svg>
        <div>0123 - 456 78 90</div>
      </div>
      <div class="contact__row">
        <svg class="contact__icon" viewBox="0 0 16 14" aria-hidden="true"><text x="0" y="12.5" font-size="15" font-weight="700" stroke="none" font-family="Arimo, sans-serif">@</text></svg>
        <div>jonas.vetter@kvl.de</div>
      </div>
      <div class="contact__row">
        <svg class="contact__icon" viewBox="0 0 16 14" aria-hidden="true" fill="none"><g fill="none" stroke-width="0.9"><circle cx="8" cy="7" r="6.3"/><ellipse cx="8" cy="7" rx="2.8" ry="6.3"/><path d="M1.7 7h12.6M2.6 3.8h10.8M2.6 10.2h10.8"/></g></svg>
        <div>www.laufbahnwechsel-beispiel.de</div>
      </div>
    </div>
  </article>

  <article class="card card--merivon">
    <svg class="card__panel" viewBox="0 0 342 221" aria-hidden="true">
      <path d="M0 0 H114 A157 157 0 0 1 103 221 H0 Z"/>
    </svg>
    <div class="brand-mark"><span class="brand-mark__dot"></span><span>MERIVON</span></div>
    <div class="holder">
      <div class="holder__name">Jonas Vetter</div>
      <div class="holder__role">Position</div>
    </div>
    <div class="contact">
      <div class="contact__brand">merivon.de</div>
      <div class="contact__owner">eine Marke der KVL GmbH</div>
      <div class="contact__row contact__row--address">
        <svg class="contact__icon" viewBox="0 0 16 18" aria-hidden="true"><path d="M8 1a6 6 0 0 0-6 6c0 4.5 6 10 6 10s6-5.5 6-10a6 6 0 0 0-6-6z" fill="none" stroke-width="1.6"/><circle cx="8" cy="7" r="2.2" stroke="none"/></svg>
        <div>Lindenweg 14<br>86999 Erlenbach</div>
      </div>
      <div class="contact__row">
        <svg class="contact__icon" viewBox="0 0 16 14" aria-hidden="true"><path stroke="none" d="M3 1l2.5-.5 2 3.5-1.5 1.5c.8 1.8 2.2 3.2 4 4l1.5-1.5 3.5 2-.5 2.5c-.5 1-1.5 1.5-2.5 1.2C6.5 12.5 2.5 8.5 1.3 3.5 1 2.5 1.8 1.5 3 1z"/></svg>
        <div>0123 - 456 78 90</div>
      </div>
      <div class="contact__row">
        <svg class="contact__icon" viewBox="0 0 16 14" aria-hidden="true"><text x="0" y="12.5" font-size="15" font-weight="700" stroke="none" font-family="Arimo, sans-serif">@</text></svg>
        <div>jonas.vetter@merivon.de</div>
      </div>
      <div class="contact__row">
        <svg class="contact__icon" viewBox="0 0 16 14" aria-hidden="true" fill="none"><g fill="none" stroke-width="0.9"><circle cx="8" cy="7" r="6.3"/><ellipse cx="8" cy="7" rx="2.8" ry="6.3"/><path d="M1.7 7h12.6M2.6 3.8h10.8M2.6 10.2h10.8"/></g></svg>
        <div>www.merivon-beispiel.de</div>
      </div>
    </div>
  </article>

</main>
</body>
</html>
```